Business card design for a dynamic IT consulting company

We need a business card design for a young firm, specialized in the Telecommunications/Consulting industry. The name of the company is Quindor and Partners Business Consulting Ltd. (Short name: Quindor and Partnes)
Quindor = solve read reverse, so we aim to be uncomplicated and solution-oriented. The small pipe in our logo is also related to the word solve. So we need a new business card design, which is simple, eye catching and something non traditional (I would probably prefer a square shaped design rather than a rectangle, but open for suggestions). Attached our logo.

Target Market(s)

Usually our customers are Tier1 Telecoms providers (Q-Netra, Palorix, etc) and their executives.

Industry/Entity Type

Business

Contact Information for Business Card

Name: Bence Tolnavari
Email: b.tolnavari@quindor.hu
Web: www.quindor.hu
Mobile: +36 30 518 2769
Title: Managing Director

Optional:
Company name: Quindor and Partners Ltd.
Address: 1087 Budapest, Tolvenka str. 28/C, Hungary

Font styles to use
Other font styles liked:
• helveticaneue_medium, Prime Regular are used now.

Colors

Designer to choose colors to be used in the design.

Requirements
Must have
• I would like to have a 2 sided design.
Nice to have
• I thought if we make the logo a bit bigger (without the company name), that could go to the back with the company name below. I though, if the pipe in the logo is somehow touchable on the business card, would be nice and unique.

```html
<!DOCTYPE html>
<html lang="en">
<head>
<meta charset="utf-8">
<title>Quindor and Partners – Business Card</title>
<link rel="stylesheet" href="https://fonts.googleapis.com/css2?family=Arimo:wght@400;700&display=swap">
<style>
  :root {
    --backdrop: #5a4838;
    --card: #f4f4f4;
    --ink-grey: #555555;
    --brand-grey: #666666;
    --brand-blue: #0a96d4;
    --brand-magenta: #b5288c;
  }
  * { box-sizing: border-box; margin: 0; padding: 0; }
  html, body {
    width: 1200px;
    height: 960px;
    overflow: hidden;
  }
  body {
    position: relative;
    background: var(--backdrop);
    font-family: "Arimo", Arial, sans-serif;
  }
  .card {
    position: absolute;
    top: 309px;
    width: 342px;
    height: 343px;
    background: var(--card);
  }
  .card--front { left: 235px; }
  .card--back { left: 623px; text-align: center; }

  .brand {
    position: absolute;
    left: 0;
    right: 0;
    top: 496px;
    top: 187px;
    display: flex;
    justify-content: center;
    align-items: center;
    gap: 8px;
  }
  .brand__name {
    font-size: 30px;
    font-weight: 400;
    color: var(--brand-grey);
    letter-spacing: -0.3px;
    line-height: 1;
  }
  .brand__dot {
    width: 9px;
    height: 9px;
    background: var(--brand-magenta);
  }

  .contact { padding-top: 86px; }
  .contact__name {
    font-size: 19px;
    font-weight: 700;
    color: var(--brand-blue);
    line-height: 22px;
  }
  .contact__title {
    font-size: 15px;
    color: var(--ink-grey);
    line-height: 20px;
    letter-spacing: 0.2px;
  }
  .contact__address {
    margin-top: 8px;
    font-size: 14px;
    color: var(--ink-grey);
    line-height: 18px;
    font-style: normal;
  }
  .contact__lines {
    margin-top: 8px;
    font-size: 14px;
    color: var(--ink-grey);
    line-height: 18px;
  }
  .contact__label {
    color: var(--brand-blue);
    font-weight: 700;
  }
  .contact__web {
    margin-top: 17px;
    font-size: 14px;
    font-weight: 700;
    color: var(--brand-blue);
    letter-spacing: 1px;
  }
</style>
</head>
<body>
  <section class="card card--front">
    <div class="brand">
      <span class="brand__name">Quindor &amp; Partners</span>
      <span class="brand__dot"></span>
    </div>
  </section>

  <section class="card card--back">
    <div class="contact">
      <h1 class="contact__name">BENCE TOLNAVARI</h1>
      <p class="contact__title">MANAGING DIRECTOR</p>
      <address class="contact__address">
        Quindor and Partners Ltd.<br>
        1087 Budapest<br>
        Tolvenka str. 28/C, Hungary
      </address>
      <p class="contact__lines">
        <span class="contact__label">P:</span> +36 30 518 2769<br>
        <span class="contact__label">E:</span> b.tolnavari@quindor.hu
      </p>
      <p class="contact__web">www.quindor.hu</p>
    </div>
  </section>
</body>
</html>
```